Velk Consulting -New consulting business in architecture, urban planning, and real estate development

We need a stationery design, including logo, business cards, etc, work for a new consulting business that works in the world of architectural, urban planning and real estate development.

The name of the company is "Velk Consulting". Velk is my last name but it of course also has the meaning 'cool' and 'hip'.

Target Market(s)

The business will provide boutique consulting services to high end clients that may include property developers, cities, etc.

Industry/Entity Type

Consultant

Contact Information for Business Card

VELK Consulting
First Name Last Name
Title
Phone number
Address
Website
Optional: Twitter handle

Logo Text

VELK Consulting

Font styles to use
Sans Serif

Colors

Designer to choose colors to be used in the design.

Requirements
Must have
• Simple design
• Easy to read font
• Modern
• Elegance
• Nice font that can be used for future reports, letters, etc.
• Good colour scheme that allows for the elegance to come through
Should not have
• Complex design ideas
• Complex logos
• Not a corporate feel and look

```html
<!DOCTYPE html>
<html lang="en">
<head>
<meta charset="utf-8">
<title>VELK Consulting – Business Card</title>
<link href="https://fonts.googleapis.com/css2?family=Montserrat:wght@400;500;800&display=swap" rel="stylesheet">
<style>
  :root{
    --page:#ececec;
    --card:#f4f4f4;
    --gold:#b3925e;
    --gold-soft:#e3d3b4;
    --ink:#222222;
    --ink-soft:#3a3a3a;
  }
  *{box-sizing:border-box;margin:0;padding:0}
  html,body{width:1200px;height:1139px;overflow:hidden;background:var(--page)}
  body{font-family:"Montserrat",sans-serif;position:relative}
  .card{
    position:absolute;left:220px;width:760px;height:434px;
    box-shadow:0 10px 28px rgba(0,0,0,.12);
  }
  .card--front{top:110px;background:var(--card)}
  .card--back{top:594px;background:var(--gold)}
  .card__border{
    position:absolute;inset:14px;border:10px solid var(--gold-soft);
  }
  .logo{
    position:absolute;font-family:"Montserrat",sans-serif;font-weight:500;
    text-align:center;line-height:1;
  }
  .logo__name{display:block;font-size:74px;letter-spacing:4px}
  .logo__sub{display:block;font-size:15px;letter-spacing:9px;margin-top:10px}
  .card--front .logo{left:70px;top:150px;width:290px;color:var(--gold)}
  .divider{position:absolute;left:392px;top:118px;width:2px;height:198px;background:var(--gold)}
  .contact{position:absolute;left:428px;top:126px;color:var(--ink-soft);font-size:15px;line-height:1.45}
  .contact__name{font-weight:800;font-size:24px;color:var(--ink);line-height:1.1}
  .contact__title{margin-bottom:10px}
  .contact__address{margin-bottom:10px}
  .contact__row{display:flex;align-items:center;gap:8px}
  .contact__row svg{width:14px;height:14px;flex:none}
  .pattern{position:absolute;inset:0;background:var(--gold)}
  .card--back .logo{left:0;right:0;top:150px;color:#f6f2ea}
</style>
</head>
<body>
  <section class="card card--front">
    <div class="card__border" role="img" aria-label="Fine gold ornamental dotted border"></div>
    <div class="logo"><span class="logo__name">VELK</span><span class="logo__sub">CONSULTING</span></div>
    <div class="divider"></div>
    <div class="contact">
      <p class="contact__name">Daniel HARTE</p>
      <p class="contact__title">Managing Director</p>
      <p class="contact__address">418 N Maple Avenue<br>Lindale, OR 97201</p>
      <p class="contact__row">
        <svg viewBox="0 0 14 14"><path d="M3 1l3 3-1.5 1.5a7 7 0 0 0 4 4L10 8l3 3-2 2C6 13 1 8 1 3z" fill="var(--gold)"/></svg>000.000.0000</p>
      <p class="contact__row">
        <svg viewBox="0 0 14 14"><rect x="2" y="1" width="10" height="12" rx="1.5" fill="none" stroke="var(--gold)" stroke-width="1.5"/></svg>000.000.0000</p>
      <p class="contact__row">
        <svg viewBox="0 0 14 14"><rect x="1" y="3" width="12" height="8" fill="none" stroke="var(--gold)" stroke-width="1.4"/><path d="M1 3l6 5 6-5" fill="none" stroke="var(--gold)" stroke-width="1.4"/></svg>daniel@northpine.ca</p>
      <p class="contact__row">
        <svg viewBox="0 0 14 14"><circle cx="7" cy="7" r="6" fill="none" stroke="var(--gold)" stroke-width="1.4"/><path d="M1 7h12M7 1c3 3 3 9 0 12M7 1c-3 3-3 9 0 12" fill="none" stroke="var(--gold)" stroke-width="1"/></svg>www.northpine.ca</p>
    </div>
  </section>

  <section class="card card--back">
    <div class="pattern" role="img" aria-label="Repeating light gold Moroccan trellis pattern on gold"></div>
    <div class="logo"><span class="logo__name">VELK</span><span class="logo__sub">CONSULTING</span></div>
  </section>
</body>
</html>
```